Emerging automotive detailing business

I am starting a small automotive detailing business in hopes of becoming a well-known detailer to work on high end cars. I would like a card to reflect the high quality and time I put into my work. The name of the company is Bright Crest Detailing. I feel like it represents racecars getting off the line at the drag strip as well as an innuendo of "Up the Ladder". I do minor paint correction such as clay barring, multi-step buffing and polishing, waxing, hand washes, etc. I am always striving to learn more and improve my work. My goal is to have total customer satisfaction. This is a female run business but I do not want it to be very girly. Elegant is okay! I have pictures of my personal wrenfield attached, they do not need to be incorporated but if you can think of a cool way to use 1 or all of them, go for it!

Target Market(s)

Anyone that owns a vehicle. Preferably high end vehicles such as Valtori, Castellverde and Morvani but I will also happily work on any car, truck or suv no matter what brand.

Industry/Entity Type

Automotive

Contact Information for Business Card

Bright Crest Detailing
Mira Tolland
4175 Quenhollow Rd
Ashmere PA 17492
Cell phone- call/text- 717-555-0148
email- brightcrestdetails@maildrop-example.com
Instagram: @brightcrestdetailing
Facebook: facebook.com/brightcrestdetailing

Requirements
Must have
• Business name, my name, address, phone number. Listing that I do minor paint correction such as clay barring, multi-step buffing and polishing, waxing, hand washes, interior cleaning, and more. (This last part was in nice to haves but I have realized that I do really want it, so I moved it to must haves.) I want something that is different and eye-catching to my customers. Some people have done this very well with cards already submitted to me, but a lot have not. I didn't mess with the "look and feel bars" much because because I am pretty open to the overall design as long as it is not your basic run of the mill design.
Nice to have
• Something car related. Maybe an appointment time/date line. I do not have a logo, but if you would like to design one and incorporate it, that would be amazing!
Should not have
• Purple and Pink colors. Boring, basic, normal card.

```html
<!DOCTYPE html>
<html lang="en">
<head>
<meta charset="utf-8">
<title>Bright Crest Detailing – Business Card</title>
<link href="https://fonts.googleapis.com/css2?family=Tinos:wght@400&family=Ubuntu:wght@400&family=Arimo:wght@400&display=swap" rel="stylesheet">
<style>
  :root {
    --page-bg: #e9e6e1;
    --ink-black: #0b0b0b;
    --paper-white: #f4f4f4;
    --paper-shade: #dcdcdc;
    --brand-red: #c9252b;
    --brand-red-dark: #a81c22;
    --text-dark: #1a1a1a;
    --text-light: #ffffff;
    --text-muted: #d6d6d6;
  }
  * { box-sizing: border-box; margin: 0; padding: 0; }
  html, body { width: 1200px; height: 902px; overflow: hidden; }
  body {
    background: var(--page-bg);
    display: flex;
    flex-direction: column;
    align-items: center;
    justify-content: center;
    gap: 56px;
  }
  .card {
    width: 600px;
    height: 343px;
    position: relative;
    overflow: hidden;
    box-shadow: 0 6px 18px rgba(0,0,0,0.25);
  }

  /* Front side */
  .card-front { background: var(--ink-black); }
  .front-band {
    position: absolute;
    left: 0; right: 0;
    top: 118px;
    height: 108px;
    background: linear-gradient(180deg, #ffffff 0%, var(--paper-white) 60%, #e6e6e6 100%);
    display: flex;
    align-items: center;
    justify-content: center;
  }
  .front-rule {
    position: absolute;
    left: 0; right: 0;
    height: 2px;
    background: var(--paper-white);
  }
  .front-rule.top { top: 110px; }
  .front-rule.bottom { top: 232px; }
  .front-title {
    font-family: "Tinos", "Times New Roman", serif;
    font-weight: 400;
    font-size: 52px;
    color: var(--brand-red);
    letter-spacing: 0.5px;
    white-space: nowrap;
  }
  .service-list {
    position: absolute;
    left: 0; right: 0;
    top: 270px;
    list-style: none;
    display: flex;
    flex-wrap: wrap;
    justify-content: center;
    gap: 4px 0;
    padding: 0 40px;
    font-family: "Arimo", Arial, sans-serif;
    font-size: 12px;
    letter-spacing: 1px;
    text-transform: uppercase;
    color: var(--text-muted);
  }
  .service-item { white-space: nowrap; }
  .service-item + .service-item::before {
    content: "";
    display: inline-block;
    width: 4px; height: 4px;
    margin: 0 10px 2px;
    background: var(--brand-red);
  }

  /* Back side */
  .card-back {
    background: linear-gradient(180deg, #ffffff 0%, var(--paper-white) 55%, var(--paper-shade) 100%);
  }
  .back-title {
    position: absolute;
    left: 0; right: 0;
    top: 76px;
    text-align: center;
    font-family: "Tinos", "Times New Roman", serif;
    font-weight: 400;
    font-size: 52px;
    color: var(--text-dark);
    white-space: nowrap;
  }
  .back-divider-band {
    position: absolute;
    left: 0; right: 0;
    top: 200px;
    height: 16px;
    background: var(--ink-black);
  }
  .back-info-band {
    position: absolute;
    left: 0; right: 0;
    top: 216px;
    bottom: 0;
    background: linear-gradient(180deg, var(--brand-red) 0%, var(--brand-red-dark) 100%);
    display: flex;
    align-items: center;
  }
  .owner-name {
    width: 265px;
    text-align: center;
    font-family: "Ubuntu", Arial, sans-serif;
    font-size: 30px;
    color: var(--text-light);
  }
  .info-rule {
    width: 1px;
    height: 96px;
    background: rgba(255,255,255,0.85);
  }
  .contact-list {
    list-style: none;
    padding-left: 16px;
    font-family: "Arimo", Arial, sans-serif;
    font-size: 13px;
    color: var(--text-light);
    line-height: 22px;
  }
  .contact-item {
    display: flex;
    align-items: center;
    gap: 8px;
    white-space: nowrap;
  }
  .contact-icon { width: 13px; height: 13px; flex: none; }
</style>
</head>
<body>

  <section class="card card-front" aria-label="Card front">
    <div class="front-rule top"></div>
    <div class="front-band">
      <h1 class="front-title">Bright Crest Detailing</h1>
    </div>
    <div class="front-rule bottom"></div>
    <ul class="service-list" aria-label="Services">
      <li class="service-item">Clay Barring</li>
      <li class="service-item">Multi-Step Buffing &amp; Polishing</li>
      <li class="service-item">Waxing</li>
      <li class="service-item">Hand Washes</li>
      <li class="service-item">Interior Cleaning &amp; More</li>
    </ul>
  </section>

  <section class="card card-back" aria-label="Card back">
    <h2 class="back-title">Bright Crest Detailing</h2>
    <div class="back-divider-band"></div>
    <div class="back-info-band">
      <p class="owner-name">Mira Tolland</p>
      <div class="info-rule"></div>
      <ul class="contact-list">
        <li class="contact-item">
          <svg class="contact-icon" viewBox="0 0 13 13" aria-hidden="true">
            <rect width="13" height="13" rx="1.5" fill="#fff"/>
            <path d="M3.2 2.8c.5-.3 1-.2 1.3.3l.7 1.2c.2.4.1.8-.2 1.1l-.5.4c.4 1 1.2 1.8 2.2 2.2l.4-.5c.3-.3.7-.4 1.1-.2l1.2.7c.5.3.6.8.3 1.3-.6 1-1.6 1.1-2.6.6C4.7 9 3.9 8.2 2.9 6.4c-.5-1-.4-2.8.3-3.6z" fill="#c9252b"/>
          </svg>
          717-555-0148
        </li>
        <li class="contact-item">
          <svg class="contact-icon" viewBox="0 0 13 13" aria-hidden="true">
            <rect width="13" height="13" rx="1.5" fill="#fff"/>
          </svg>
          @brightcrestdetailing
        </li>
        <li class="contact-item">
          <svg class="contact-icon" viewBox="0 0 13 13" aria-hidden="true">
            <rect width="13" height="13" rx="1.5" fill="#fff"/>
            <rect x="2.5" y="4" width="8" height="5.5" fill="none" stroke="#c9252b" stroke-width="1"/>
            <path d="M2.5 4l4 3 4-3" fill="none" stroke="#c9252b" stroke-width="1"/>
          </svg>
          brightcrestdetails@maildrop-example.com
        </li>
        <li class="contact-item">
          <svg class="contact-icon" viewBox="0 0 13 13" aria-hidden="true">
            <rect width="13" height="13" rx="1.5" fill="#fff"/>
            <path d="M6.5 2.3a2.8 2.8 0 0 1 2.8 2.8c0 2-2.8 5.4-2.8 5.4S3.7 7.1 3.7 5.1a2.8 2.8 0 0 1 2.8-2.8z" fill="#c9252b"/>
            <circle cx="6.5" cy="5.1" r="1" fill="#fff"/>
          </svg>
          4175 Quenhollow Rd, Ashmere PA 17492
        </li>
      </ul>
    </div>
  </section>

</body>
</html>
```